Cafe menu flyer design

I need if possible A4 double sided menus. Two exemplars: first will contain breakfast menu on one side & refreshments menu on the other side, second exemplar will contain lunch menu on one side & refreshments menu on the other side. We do not need a description of the cafe or any history on these flyers, but design should reflect our surroundings and activities this area. We are located in main ski resort in UK-Cairngorm Mountains, right on the main ski road. The slopes are only 2 miles away from us. We are also very popular with wild life enthusiasts. Continues in design brief!

Cafe

```html
<!DOCTYPE html>
<html lang="en">
<head>
<meta charset="utf-8">
<title>Morag's @ Kinbeg Cafe – Menu</title>
<link href="https://fonts.googleapis.com/css2?family=Playfair+Display:ital,wght@1,900&family=Nunito+Sans:wght@700;800&display=swap" rel="stylesheet">
<style>
  :root {
    --sky: #8fcdee;
    --mountain: #85738d;
    --hill-green: #7fa82a;
    --night: #1d1c3c;
    --ink: #111111;
    --white: #ffffff;
    --robin: #d3262c;
  }
  * { box-sizing: border-box; margin: 0; padding: 0; }
  html, body { width: 1200px; height: 927px; overflow: hidden; }
  body { font-family: "Nunito Sans", Arial, sans-serif; }
  .menu {
    position: relative; width: 1200px; height: 927px; overflow: hidden;
    background: var(--night); color: var(--white);
  }
  .landscape {
    position: absolute; left: 0; top: 0; width: 1200px; height: 280px;
    background: linear-gradient(180deg, var(--sky) 0%, var(--sky) 18%, var(--mountain) 34%, var(--mountain) 80%, var(--hill-green) 86%, var(--hill-green) 100%);
  }
  .brand {
    position: absolute; left: 98px; top: 100px;
    font-family: "Playfair Display", Georgia, serif; font-style: italic; font-weight: 900;
    font-size: 86px; line-height: 1; color: var(--ink); letter-spacing: 1px;
  }
  .contact {
    position: absolute; left: 525px; top: 192px;
    font-size: 15px; font-weight: 800; color: var(--ink);
  }
  .social {
    position: absolute; left: 1075px; top: 72px; width: 112px; text-align: center;
    font-size: 15px; font-weight: 800; line-height: 1.1; color: var(--white);
  }
  .social-square {
    display: block; width: 98px; height: 98px; margin: 0 auto 8px;
    background: var(--mountain); border: 2px solid var(--white); border-radius: 14px;
  }
  .column { position: absolute; top: 308px; font-size: 17px; font-weight: 800; line-height: 21px; }
  .column--breakfast { left: 69px; width: 540px; }
  .column--drinks { left: 657px; width: 460px; }
  .section-title { margin-bottom: 0; }
  .item { display: flex; align-items: flex-end; }
  .item .name { flex: 0 0 auto; }
  .column--breakfast .item .name { width: 403px; }
  .column--drinks .item .name { width: 402px; }
  .item .price { white-space: nowrap; }
  .note { display: block; }
  .robin {
    position: absolute; left: 68px; top: 745px; width: 205px; height: 150px;
    background: var(--robin); border-radius: 60% 40% 45% 55% / 50% 50% 40% 40%;
  }
  .info {
    position: absolute; left: 297px; top: 783px; width: 305px;
    font-size: 17px; font-weight: 800; line-height: 21px;
  }
</style>
</head>
<body>
<main class="menu">
  <div class="landscape" role="img" aria-label="Illustrated mountain range with white clouds against a blue sky and a green band of treetops"></div>
  <h1 class="brand">Morag's @ Kinbeg Cafe</h1>
  <p class="contact">Strathkin, Kinbeg, PH99 4ZX.&nbsp; Tel:01234567890</p>
  <div class="social"><span class="social-square"></span>Follow us online!</div>

  <section class="column column--breakfast">
    <h2 class="section-title" style="font-size:17px;font-weight:800;">BREAKFAST 9AM - 12NOON</h2>
    <div class="item"><span class="name">Small breakfast (bacon, egg, sausage)</span><span class="price">£5.50</span></div>
    <span class="note">Large brteakfast (bacon, egg, sausage,<br>black pudding, potato scone, beans, tomato)£7.95</span>
    <span class="note">BOTH BREAKFASTS INCLUDE TEA/COFFE/PLAIN HOT CH<br>OCOLATE &amp; ONE SLICE OF TOAST. ONE FREE REFILL DRINK.</span>
    <span class="note">Pancake breakfast. Three pancakes served with hot forest</span>
    <div class="item"><span class="name">berry sauce and maple syrup</span><span class="price">£4.95</span></div>
    <div class="item"><span class="name">Add three rushers of bacon</span><span class="price">£6.95</span></div>
    <div class="item"><span class="name">Round of toast,served with butter and jam</span><span class="price">£2.00</span></div>
    <div class="item"><span class="name">Beans on toast</span><span class="price">£3.50</span></div>
    <div class="item"><span class="name">Beans &amp; egg on toast</span><span class="price">£4.00</span></div>
    <div class="item"><span class="name">Beans &amp; bacon on toast</span><span class="price">£4.50</span></div>
    <div class="item"><span class="name">Bacon roll</span><span class="price">£2.90</span></div>
    <div class="item"><span class="name">Lorne roll</span><span class="price">£2.50</span></div>
    <div class="item"><span class="name">Black pudding roll</span><span class="price">£2.50</span></div>
    <div class="item"><span class="name">Fried egg roll</span><span class="price">£2.00</span></div>
    <div class="item"><span class="name">2 item roll</span><span class="price">£4.00</span></div>
    <div class="item"><span class="name">Rolls with assorted cold fillings</span><span class="price">£2.20 - £3.20</span></div>
    <div class="item"><span class="name">Pies assorted</span><span class="price">£2.50</span></div>
  </section>

  <div class="robin" role="img" aria-label="Simple red bird silhouette illustration"></div>
  <p class="info">Gluten free bread, cakes and veg-gie breakfast available- ask staff! At the hight of the season evening meals vailable. Ask staff for more information.</p>

  <section class="column column--drinks">
    <h2 class="section-title" style="font-size:17px;font-weight:800;">REFRESHMENTS</h2>
    <div class="item"><span class="name">Tea</span><span class="price">£1.50</span></div>
    <span class="note">Filter Coffee, decaf coffee, plain hot chocolate<br>£2.00</span>
    <div class="item"><span class="name">Selection of herbal teas</span><span class="price">£2.00</span></div>
    <div class="item"><span class="name">Specialty black tea with your choice of syrup</span><span class="price">£2.50</span></div>
    <span class="note">&nbsp;strawberry, raspberry, apple &amp; mint tea</span>
    <div class="item"><span class="name">Assorted premium “Leaf Loft” teas</span><span class="price">£2.50</span></div>
    <div class="item"><span class="name">Hot chocolate with cream</span><span class="price">£2.20</span></div>
    <div class="item"><span class="name">Hot chocolate with marsh mallows</span><span class="price">£2.20</span></div>
    <div class="item"><span class="name">Hot chocolate with cream &amp; marsh mallows</span><span class="price">£2.20</span></div>
    <div class="item"><span class="name">Hot chocolate with brandy</span><span class="price">£3.50</span></div>
    <div class="item"><span class="name">Hot chocolate with brandy, marsh mallows &amp;<br>cream</span><span class="price">£4.50</span></div>
    <div class="item"><span class="name">Cafe Latte/Cappucino</span><span class="price">£2.50</span></div>
    <div class="item"><span class="name">Squirrel Latte</span><span class="price">£3.50</span></div>
    <div class="item"><span class="name">Chocolate Latte</span><span class="price">£3.50</span></div>
    <div class="item"><span class="name">Cinnamon Latte</span><span class="price">£3.50</span></div>
    <div class="item"><span class="name">Caramel Latte</span><span class="price">£3.50</span></div>
    <div class="item"><span class="name">Butterscotch Latte</span><span class="price">£3.50</span></div>
    <div class="item"><span class="name">Gingerbread Latte</span><span class="price">£3.50</span></div>
    <div class="item"><span class="name">Mocha</span><span class="price">£3.50</span></div>
    <div class="item"><span class="name">Glass of milk</span><span class="price">£1.20</span></div>
    <div class="item"><span class="name">Milkshakes</span><span class="price">£2.00</span></div>
    <div class="item"><span class="name">Still or Sparkling water</span><span class="price">£1.80</span></div>
    <div class="item"><span class="name">Cans of juice</span><span class="price">£1.60</span></div>
    <div class="item"><span class="name">Cartons of juice</span><span class="price">£1.30</span></div>
  </section>
</main>
</body>
</html>
```